Lamp Over The Valleys- a non profit locin TZ , east Africa. Needing to attract donors.

A flyer for donors /potential partners. showing what their giving has accomplished this year. An Encouraging way to say thank you at the same time informing the partner of the amazing things God is doing with their generous, faithful giving. We will need to print/email. Thank you for considering this project. Your efforts help in educating and feeding 225 street children, providing a safe haven and trade school for hundreds of women and abused teenagers, medical ship on the longest lake in the world going into unreached people groups, a Bible College Training up pastors to plant churches all over TZ, Congo, Burundi and beyond, youth and children’s kids clubs and youth camps. These are the main areas of lamp over the valleys. Bible college, primary school, trade schools, youth camps/kids clubs. We need help in making sure readers will be drawn to seeing/reading more which leads to donations without overwhelming with too much info. HELP! I can tell you about Jesus I have even authored 7 books, but making s flyer that makes sense it out of my wheelhouse. Again, thank you.

I do not want longer I need quicker and paid for a 3 day quote. All pictures and logo are on our website. I have tried to send pictures but they won’t send. Please look at. Www.lampoverthevalleystz.example

Target Market(s)

Professional adults, large companies, donors

Industry/Entity Type

Non profit missionary Lamp over the Valleys in Tanzania, Congo, USA and soon to be Canada.

Requirements
Must have
• Color professional pictures, feel good, exciting want to be apart of what God is doing
Nice to have
• Glossy trifold
Should not have
• Fly in the face, guilt feeling, animals in Africa

```html
<!DOCTYPE html>
<html lang="en">
<head>
<meta charset="UTF-8">
<title>Happy Thanksgiving – Thank You to Our Donors</title>
<link href="https://fonts.googleapis.com/css2?family=Open+Sans:wght@400;600&family=Montserrat:wght@800;900&family=Mr+Dafoe&family=Bowlby+One&display=swap" rel="stylesheet">
<style>
  :root{
    --backdrop:#d9d9d9;
    --navy:#2e3f58;
    --navy-soft:#34475f;
    --navy-deep:#26354b;
    --cream:#fdebd0;
    --white:#ffffff;
    --rust:#d0441a;
    --orange:#f28a30;
    --amber:#f0a030;
    --pink:#ef5f9f;
    --sky:#6ec8e6;
    --yellow:#f6c200;
  }
  *{box-sizing:border-box;margin:0;padding:0}
  html,body{width:1200px;height:1200px;overflow:hidden;background:var(--backdrop)}
  .canvas{width:1200px;height:1200px;display:flex;align-items:center;justify-content:center}
  .flyer{position:relative;width:848px;height:1200px;background:var(--navy);overflow:hidden}
  .flyer__backdrop{position:absolute;inset:0}
  .decor{position:absolute}
  .headline__happy,.headline__script,.headline__lead{position:absolute;left:0;right:0;text-align:center}
  .headline__happy{top:180px;font-family:"Montserrat",sans-serif;font-weight:900;font-size:50px;line-height:1;letter-spacing:3px;color:var(--rust);padding-right:170px}
  .headline__script{top:215px;font-family:"Mr Dafoe",cursive;font-weight:400;font-size:130px;line-height:1.1;color:var(--cream)}
  .headline__lead{top:378px;font-family:"Open Sans",sans-serif;font-weight:600;font-size:32px;line-height:1.2;color:var(--white);padding-left:140px}
  .tiles{position:absolute;left:0;right:0;display:flex;justify-content:center;gap:14px}
  .tiles--thank{top:480px}
  .tiles--you{top:620px;padding-left:150px}
  .tile{width:118px;height:124px;display:flex;align-items:center;justify-content:center;font-family:"Bowlby One",sans-serif;font-size:86px;color:var(--cream);box-shadow:0 3px 0 rgba(0,0,0,.15)}
  .tile--orange{background:var(--orange);transform:rotate(-2deg)}
  .tile--pink{background:var(--pink);transform:rotate(2deg)}
  .tile--sky{background:var(--sky);transform:rotate(-1deg)}
  .tile--yellow{background:var(--yellow);transform:rotate(3deg)}
  .donors{position:absolute;left:0;right:0;top:772px;text-align:center;font-family:"Montserrat",sans-serif;font-weight:800;font-size:56px;line-height:1.1;letter-spacing:1px;color:var(--cream)}
  .impact{position:absolute;left:112px;right:112px;top:862px;text-align:center;font-family:"Open Sans",sans-serif;font-size:19px;line-height:1.5;color:var(--white)}
</style>
</head>
<body>
<main class="canvas">
  <article class="flyer">
    <svg class="flyer__backdrop" width="848" height="1200" viewBox="0 0 848 1200" aria-hidden="true">
      <path d="M0 0H848V230C700 180 560 210 420 160 300 120 180 60 0 90Z" fill="var(--navy-soft)"/>
      <path d="M0 330C120 300 150 420 130 560 110 700 40 760 0 780Z" fill="var(--navy-deep)"/>
      <path d="M848 520C760 540 730 640 760 760 790 880 820 940 848 950Z" fill="var(--navy-deep)"/>
      <path d="M0 1120C160 1060 320 1100 460 1080 620 1060 740 1100 848 1080V1200H0Z" fill="var(--navy-soft)"/>
    </svg>

    <svg class="decor" style="left:-40px;top:420px" width="120" height="110" viewBox="0 0 120 110" role="img" aria-label="Orange maple leaf illustration">
      <ellipse cx="60" cy="55" rx="58" ry="52" fill="var(--amber)"/>
    </svg>
    <svg class="decor" style="left:560px;top:30px" width="120" height="120" viewBox="0 0 120 120" role="img" aria-label="Dark navy leaf sprig illustration">
      <ellipse cx="60" cy="60" rx="50" ry="56" fill="var(--navy-deep)"/>
    </svg>
    <svg class="decor" style="left:100px;top:432px" width="120" height="36" viewBox="0 0 120 36" role="img" aria-label="Rust oak leaf illustration">
      <ellipse cx="60" cy="18" rx="58" ry="16" fill="var(--rust)"/>
    </svg>
    <svg class="decor" style="left:712px;top:640px" width="100" height="90" viewBox="0 0 100 90" role="img" aria-label="Rust maple leaf illustration">
      <ellipse cx="50" cy="45" rx="48" ry="42" fill="var(--rust)"/>
    </svg>
    <svg class="decor" style="left:772px;top:880px" width="110" height="130" viewBox="0 0 110 130" role="img" aria-label="Orange autumn leaf illustration">
      <ellipse cx="55" cy="65" rx="53" ry="62" fill="var(--amber)"/>
    </svg>
    <svg class="decor" style="left:60px;top:1085px" width="160" height="130" viewBox="0 0 160 130" role="img" aria-label="Red autumn leaf illustration">
      <ellipse cx="80" cy="75" rx="78" ry="58" fill="var(--rust)"/>
    </svg>
    <svg class="decor" style="left:10px;top:640px" width="80" height="180" viewBox="0 0 80 180" role="img" aria-label="Dark navy fern sprig illustration">
      <ellipse cx="40" cy="90" rx="36" ry="86" fill="var(--navy-deep)"/>
    </svg>

    <header class="headline">
      <p class="headline__happy">HAPPY</p>
      <h1 class="headline__script">Thanks Giving</h1>
      <p class="headline__lead">In all things give</p>
    </header>

    <div class="tiles tiles--thank" aria-label="THANK">
      <span class="tile tile--orange">T</span>
      <span class="tile tile--pink">H</span>
      <span class="tile tile--sky">A</span>
      <span class="tile tile--orange">N</span>
      <span class="tile tile--yellow">K</span>
    </div>
    <div class="tiles tiles--you" aria-label="YOU">
      <span class="tile tile--sky">Y</span>
      <span class="tile tile--yellow">O</span>
      <span class="tile tile--pink">U</span>
    </div>

    <h2 class="donors">TO OUR DONORS</h2>

    <p class="impact">For their efforts help in educating and feeding 225 street children, providing a safe haven and trade school for hundreds of women and abused teenagers, medical ship on the longest lake in the world going into unreached people groups, a Bible College Training up pastors to plant churches all over TZ, Congo, Burundi and beyond, youth and children’s kids clubs and youth camps.</p>
  </article>
</main>
</body>
</html>
```